Hvac and insulation company needs good looking business card design

We are hvac and insulation company and looking for a new business cards that look to today standards designs

Target Market(s)

homeowners

Industry/Entity Type

Hvac

Contact Information for Business Card

Name: Walter Brinoku
Home comfort consultant
address: 4827 Dunmore St #215 Oakland, CA 94619
office: 888-316-2790
cell: 510-742-3185
Lic.# 584261
Email: walter@corvane-hvac.com
Web: corvane-hvac.com

Requirements
Must have
• clean and sleek look
Nice to have
• simple with a clean look
Should not have
• to busy business card

```html
<!DOCTYPE html>
<html lang="en">
<head>
<meta charset="utf-8">
<title>Corvane Home Solutions – Business Card</title>
<link href="https://fonts.googleapis.com/css2?family=Open+Sans:wght@400;500;600&display=swap" rel="stylesheet">
<style>
  :root {
    --page-bg: #e9eaea;
    --card-bg: #ffffff;
    --brand-orange: #f08522;
    --ink: #222222;
    --card-shadow: rgba(0, 0, 0, 0.18);
  }
  html, body {
    margin: 0;
    padding: 0;
    width: 1000px;
    height: 1200px;
    overflow: hidden;
    background: var(--page-bg);
    font-family: "Open Sans", Arial, sans-serif;
    color: var(--ink);
  }
  .canvas {
    position: relative;
    width: 1000px;
    height: 1200px;
  }
  .card {
    position: absolute;
    left: 215px;
    width: 580px;
    height: 356px;
    background: var(--card-bg);
    box-shadow: 0 2px 8px var(--card-shadow);
  }
  .card--front {
    top: 218px;
    border-radius: 4px 52px 4px 52px;
  }
  .card--back {
    top: 607px;
    border-radius: 52px 4px 52px 4px;
  }
  .holder-name {
    position: absolute;
    left: 41px;
    top: 62px;
    margin: 0;
    font-size: 19px;
    font-weight: 600;
    letter-spacing: 0.2px;
    text-transform: uppercase;
    color: var(--brand-orange);
  }
  .holder-title {
    position: absolute;
    left: 41px;
    top: 89px;
    margin: 0;
    font-size: 15px;
  }
  .contact-list {
    position: absolute;
    left: 41px;
    top: 141px;
    margin: 0;
    padding: 0;
    list-style: none;
    font-size: 15px;
    line-height: 21px;
  }
  .contact-list li {
    display: flex;
    align-items: center;
  }
  .contact-icon {
    width: 12px;
    height: 12px;
    margin-right: 7px;
    fill: var(--brand-orange);
  }
  .address {
    position: absolute;
    left: 41px;
    top: 253px;
    margin: 0;
    font-style: normal;
    font-size: 15px;
    line-height: 21px;
  }
  .license {
    position: absolute;
    left: 450px;
    top: 280px;
    margin: 0;
    font-size: 15px;
    color: var(--brand-orange);
  }
  .brand-mark {
    display: flex;
    align-items: center;
    color: var(--brand-orange);
    font-weight: 500;
  }
  .brand-mark__square {
    background: var(--brand-orange);
    flex: none;
  }
  .card--front .brand-mark {
    position: absolute;
    left: 344px;
    top: 92px;
    font-size: 40px;
  }
  .card--front .brand-mark__square {
    width: 44px;
    height: 44px;
    margin-right: 14px;
  }
  .card--back .brand-mark {
    position: absolute;
    left: 58px;
    top: 122px;
    font-size: 84px;
    line-height: 1;
  }
  .card--back .brand-mark__square {
    width: 80px;
    height: 80px;
    margin-right: 24px;
  }
</style>
</head>
<body>
<main class="canvas">

  <section class="card card--front" aria-label="Business card front">
    <h1 class="holder-name">Walter Brinoku</h1>
    <p class="holder-title">Home Comfort Consultant</p>

    <ul class="contact-list">
      <li>
        <svg class="contact-icon" viewBox="0 0 12 12" aria-hidden="true"><path d="M1 4c0-2 2-3 5-3s5 1 5 3v1H8.5V3.6C7.8 3.3 4.2 3.3 3.5 3.6V5H1zM3 6h6l1.5 4.5h-9z"/></svg>
        888-316-2790
      </li>
      <li>
        <svg class="contact-icon" viewBox="0 0 12 12" aria-hidden="true"><path d="M3 0h6a1 1 0 0 1 1 1v10a1 1 0 0 1-1 1H3a1 1 0 0 1-1-1V1a1 1 0 0 1 1-1zm.5 1.5v7.5h5V1.5zM6 10a.6.6 0 1 0 0 1.2.6.6 0 0 0 0-1.2z"/></svg>
        510-742-3185
      </li>
      <li>
        <svg class="contact-icon" viewBox="0 0 12 12" aria-hidden="true"><path d="M0 2.5h12v7H0zM1 3.5v.3l5 3.2 5-3.2v-.3zm0 1.5v3.5h10V5L6 8.2z"/></svg>
        walter@corvane-hvac.com
      </li>
      <li>
        <svg class="contact-icon" viewBox="0 0 12 12" aria-hidden="true"><circle cx="6" cy="6" r="6"/><path d="M3 3.5c1 0 1.5.8 2.5.6s1 1 .3 1.6-1.8.2-2 1.2S2.5 8 2 6.5zM8 7.5c.8-.5 1.8 0 1.6 1s-1.2 1.3-1.8.8z" fill="#ffffff"/></svg>
        corvane-hvac.com
      </li>
    </ul>

    <address class="address">
      4827 Dunmore St #215<br>
      Oakland, CA 94619
    </address>

    <div class="brand-mark">
      <span class="brand-mark__square" aria-hidden="true"></span>
      corvane
    </div>

    <p class="license">Lic.# 584261</p>
  </section>

  <section class="card card--back" aria-label="Business card back">
    <div class="brand-mark">
      <span class="brand-mark__square" aria-hidden="true"></span>
      corvane
    </div>
  </section>

</main>
</body>
</html>
```